Meadowlight Soaps Business Card

The new business card design will incorporate my new logo components designed by one of your designers. Meadowlight Soaps creates high quality soaps and bath products. They would be suited for a Spa, Bed and Breakfast, Boutique environment. The look should be a white background.
Classy, soft and using the colour palet of the logo. The card will be two sided.

Reason: Need more time to make some changes and decide.

Target Market(s)

Looking to appeal to an upper end market. Spas, boutiques, independent gift stores, bridal salons, bed and breakfast, etc. I want the card to impart a sense of elegance, tranquility and Meadowlight. But also quality and value.

Industry/Entity Type

Business

Font styles to use
Sans Serif
Script

Requirements
Must have
• My logo on the front. But also on the back but faded out to allow written notes on the back.
On the front : Carol Pritchett
Owner/Creator
48 Fenwick Rd
Guelph, Ont N4K 2P9
519.402.6183
Creating Quality Handcrafted Soaps And Bath Products
Custom and Wholesale Orders Welcome
Www.meadowlightsoaps.ca
www.friendpage.net / MeadowlightSoapandBath
info@meadowlightsoaps.ca

```html
<!DOCTYPE html>
<html lang="en">
<head>
<meta charset="utf-8">
<title>Meadowlight Soaps Business Card</title>
<link href="https://fonts.googleapis.com/css2?family=Lato:wght@300;400&display=swap" rel="stylesheet">
<style>
  :root {
    --bg: #ece9e4;
    --card: #ffffff;
    --teal: #9fc4bb;
    --teal-soft: #c9ddd7;
    --sand: #e6d3c2;
    --grey: #cfcfcf;
    --ink: #3c3c3c;
    --rule: #5a5a5a;
  }
  * { box-sizing: border-box; margin: 0; padding: 0; }
  html, body { width: 1200px; height: 886px; overflow: hidden; }
  body {
    background: var(--bg);
    font-family: "Lato", Arial, sans-serif;
    color: var(--ink);
    position: relative;
  }
  .card {
    position: absolute;
    top: 288px;
    width: 540px;
    height: 309px;
    background: var(--card);
    border-radius: 14px;
    box-shadow: 0 2px 6px rgba(0,0,0,0.12);
    overflow: hidden;
  }
  .card--front { left: 30px; }
  .card--back { left: 630px; }

  /* Front */
  .brand-mark {
    position: absolute;
    left: 34px; top: 58px;
    width: 150px; height: 78px;
    border-radius: 50%;
    background: radial-gradient(ellipse at center, var(--teal-soft) 0%, rgba(230,211,194,0.5) 55%, rgba(255,255,255,0) 75%);
  }
  .brand-name {
    position: absolute;
    left: 30px; top: 138px;
    font-weight: 300;
    font-size: 24px;
    color: var(--teal);
    letter-spacing: 0.5px;
    display: flex; align-items: center; gap: 8px;
  }
  .brand-name .dot {
    width: 9px; height: 9px; border-radius: 50%;
    background: var(--teal);
  }
  .owner {
    position: absolute;
    right: 34px; top: 40px;
    text-align: right;
  }
  .owner-name {
    font-weight: 300;
    font-size: 22px;
    color: var(--teal);
  }
  .owner-title {
    font-size: 12px;
    color: var(--ink);
    margin-top: 2px;
  }
  .divider {
    position: absolute;
    left: 210px; right: 118px; top: 88px;
    height: 1px;
    background: var(--teal);
  }
  .contact {
    position: absolute;
    left: 30px; bottom: 28px;
    list-style: none;
    font-size: 12px;
    line-height: 18px;
  }
  .contact li { display: flex; align-items: center; gap: 8px; }
  .contact svg { width: 10px; height: 10px; flex: none; }
  .address {
    position: absolute;
    right: 34px; bottom: 32px;
    text-align: right;
    font-size: 12px;
    line-height: 18px;
    font-style: normal;
  }

  /* Back */
  .back-mark {
    position: absolute;
    left: 40px; top: 14px;
    width: 440px; height: 150px;
    display: flex; align-items: center; justify-content: center;
    background: radial-gradient(ellipse at center, rgba(201,221,215,0.55) 0%, rgba(230,211,194,0.3) 50%, rgba(255,255,255,0) 72%);
    font-weight: 300;
    font-size: 40px;
    color: rgba(159,196,187,0.45);
    letter-spacing: 1px;
  }
  .note-label {
    position: absolute;
    left: 255px; top: 178px;
    font-weight: 300;
    font-size: 26px;
    color: var(--teal);
  }
  .note-lines { position: absolute; left: 24px; top: 0; width: 300px; height: 309px; }
  .note-lines span {
    position: absolute; left: 0; height: 1px; background: var(--rule);
  }
  .tagline {
    position: absolute;
    right: 28px; bottom: 34px;
    text-align: right;
    font-size: 14px;
    line-height: 19px;
    color: var(--ink);
  }
</style>
</head>
<body>
  <section class="card card--front" aria-label="Card front">
    <div class="brand-mark" role="img" aria-label="Soft watercolour splash in teal, sand and grey behind the company name"></div>
    <div class="brand-name"><span class="dot"></span>Meadowlight Soaps</div>

    <div class="owner">
      <div class="owner-name">Carol Pritchett</div>
      <div class="owner-title">Owner</div>
    </div>
    <div class="divider"></div>

    <ul class="contact">
      <li>
        <svg viewBox="0 0 10 10"><path d="M2 1 L4 1 L4.6 3 L3.4 3.8 Q4.3 5.8 6.2 6.6 L7 5.4 L9 6 L9 8 Q5 9 2.4 6.6 Q1 4.6 2 1Z" fill="#3c3c3c"/></svg>
        519.402.6183
      </li>
      <li>
        <svg viewBox="0 0 10 10"><circle cx="5" cy="5" r="4.2" fill="none" stroke="#3c3c3c" stroke-width="1"/><path d="M1 5 H9 M5 0.8 Q2.5 5 5 9.2 Q7.5 5 5 0.8" fill="none" stroke="#3c3c3c" stroke-width="0.8"/></svg>
        www.meadowlightsoaps.ca
      </li>
      <li>
        <svg viewBox="0 0 10 10"><rect x="0.5" y="0.5" width="9" height="9" rx="1" fill="#3c3c3c"/></svg>
        www.friendpage.net /MeadowlightSoapandBath
      </li>
    </ul>

    <address class="address">
      48 Fenwick Rd<br>
      Guelph, Ont N4K 2P9
    </address>
  </section>

  <section class="card card--back" aria-label="Card back">
    <div class="back-mark">Meadowlight Soaps</div>
    <div class="note-label">Note</div>
    <div class="note-lines" aria-hidden="true">
      <span style="top:150px; width:210px;"></span>
      <span style="top:182px; width:210px;"></span>
      <span style="top:214px; width:210px;"></span>
      <span style="top:246px; width:210px;"></span>
      <span style="top:278px; width:210px;"></span>
    </div>
    <p class="tagline">Creating Quality Handcrafted Soaps And<br>Bath Products</p>
  </section>
</body>
</html>
```